Hearthside Lending Relief

Please help us give our website a remake or a FACELIFT. It is not very good but it says what we need it to say. But the design is terrible.
I would like our new design font and logo to be used as the theme.

I also want more photos on the site.

I also want consistency with the pages so they look clean.

We want the professionals to do this, let's see what you got!

Thank you!
Updates

Project Deadline Extended
Reason: I can understand you want to be paid. So I will commit to the fee but I want you to have time to make a KICK ASS website for me dudes! Thanks

HI!  Just wanted to say thanks for your time on these.  A lot are great.  However the firefighters have nothing to do with Foreclosure.  We are saving peoples homes from the bank taking them and selling them.   I LOVE the house photos and the families on the website.  That is the direction we like.  THanks.

THANK U ALL FOR THE WORK!   I like a few ending in the numbers: 147  733  693  536  620  478  727  508     I will go over them and choose one soon.  Thank you.   You will be paid shortly. 

Requirements
Must have
• Bright, Upbeat photos. Color scheme should be in order. We like icons on the bottom. not just text.

```html
<!DOCTYPE html>
<html lang="en">
<head>
<meta charset="utf-8">
<title>Hearthside Lending Relief – About Us</title>
<link rel="stylesheet" href="https://fonts.googleapis.com/css2?family=Arimo:wght@400;700&family=Tinos:wght@400;700&display=swap">
<style>
:root{
  --red:#e3262a;
  --blue:#1c8ad1;
  --text:#5a5a5a;
  --dark:#333;
  --page:#ebecee;
  --white:#fff;
  --nav:#58595b;
  --nav-dark:#3f4042;
  --rule:#c9cacc;
  --footer:#0c3a6b;
  --footer-deep:#06284e;
  --footer-head:#4ab0e8;
}
*{margin:0;padding:0;box-sizing:border-box}
html,body{width:815px;height:1200px;overflow:hidden}
body{position:relative;background:var(--page);font-family:'Arimo',Arial,sans-serif;color:var(--text)}
.abs{position:absolute}

.site-header{left:0;top:0;width:815px;height:146px;background:var(--white)}
.util-tab{left:621px;top:0;width:88px;height:19px;background:#e4e5e7;font-size:8px;color:#777;text-align:center;line-height:20px}
.brand{left:116px;top:40px;display:flex;align-items:center;gap:10px}
.brand-mark{width:56px;height:56px;border-radius:50%;background:var(--red)}
.brand-name{font-family:'Arimo',Arial,sans-serif;font-weight:700;font-size:15px;line-height:17px;color:var(--red);text-transform:uppercase;width:170px}
.call{left:456px;top:65px;font-size:12px;color:#555}
.phone{left:559px;top:54px;font-family:'Tinos','Times New Roman',serif;font-size:29px;color:var(--blue)}

.main-nav{left:105px;top:105px;width:604px;height:31px;background:linear-gradient(#6a6b6d,var(--nav-dark));display:flex;align-items:center;border-radius:2px}
.nav-item{height:31px;display:flex;align-items:center;justify-content:center;color:#fff;font-size:11px;border-right:1px solid #4a4b4d;letter-spacing:.2px}
.nav-item.home{width:73px}
.nav-item.active{width:81px;background:var(--nav-dark)}
.nav-item.w1{width:82px}.nav-item.w2{width:136px}.nav-item.w3{width:98px;border-right:0}
.search{margin-left:2px;width:122px;height:20px;background:#fff;display:flex;align-items:center;justify-content:space-between;padding-left:6px;font-size:8px;color:#999}
.search-btn{width:18px;height:18px;background:var(--red);margin-right:1px;display:flex;align-items:center;justify-content:center}

.photo{border-radius:2px}
.about-photo{left:106px;top:188px;width:248px;height:164px;background:linear-gradient(160deg,#3d6fb0 0%,#7aa0c8 45%,#6a8a3a 80%,#4e6b2a 100%)}
.section-title{font-family:'Tinos','Times New Roman',serif;font-weight:700;font-variant:small-caps;color:var(--red);font-size:21px;letter-spacing:.5px;border-bottom:1px solid var(--rule);padding-bottom:0}
.copy{font-size:11.4px;line-height:17px;text-align:justify;color:var(--text)}

.member{left:112px;width:250px;height:80px}
.member-photo{left:0;top:0;width:108px;height:78px}
.member-bio{left:128px;top:5px;width:122px;font-size:9px;line-height:13.3px}
.member-bio b{display:block;color:var(--dark);font-size:9px}

.site-footer{left:0;top:985px;width:815px;height:215px;background:radial-gradient(ellipse at 40% 30%,#115092 0%,var(--footer) 45%,var(--footer-deep) 100%)}
.foot-col h3{font-size:13px;color:var(--footer-head);font-weight:700;margin-bottom:6px}
.foot-col li{list-style:none;font-size:7.6px;color:#fff;line-height:13.3px}
.news-title{left:379px;top:1027px;color:#fff;font-size:13px;font-weight:700}
.email{left:377px;top:1054px;width:150px;height:23px;background:#fff;border-radius:4px;font-size:8.5px;color:#888;padding-left:9px;line-height:23px}
.subscribe{left:535px;top:1054px;width:74px;height:24px;background:var(--red);border-radius:4px;color:#fff;font-weight:700;font-size:11px;text-align:center;line-height:24px}
.social{top:1055px;width:20px;height:20px;background:#e8e8e8;border-radius:3px}
.foot-rule{left:0;top:1133px;width:815px;height:1px;background:#1d4d80}
.legal{left:119px;top:1149px;font-size:7.8px;color:#fff}
.copyright{left:119px;top:1163px;font-size:7.8px;color:var(--footer-head)}
</style>
</head>
<body>
<header class="abs site-header">
  <div class="abs util-tab">Login &nbsp;|&nbsp; Contacts</div>
  <div class="abs brand"><span class="brand-mark"></span><span class="brand-name">Hearthside Lending Relief</span></div>
  <div class="abs call">Call Toll-Free Now</div>
  <div class="abs phone">800-555-0142</div>
  <nav class="abs main-nav">
    <div class="nav-item home"><svg width="15" height="13" viewBox="0 0 15 13"><path d="M7.5 0 0 6.5h2V13h4V9h3v4h4V6.5h2z" fill="#fff"/></svg></div>
    <div class="nav-item active">ABOUT US</div>
    <div class="nav-item w1">SERVICES</div>
    <div class="nav-item w2">FINANCING OPTIONS</div>
    <div class="nav-item w3">CONTACT US</div>
    <div class="search">Search...<span class="search-btn"><svg width="10" height="10" viewBox="0 0 10 10"><circle cx="6" cy="4" r="3" fill="none" stroke="#fff" stroke-width="1.4"/><path d="M4 6 1 9" stroke="#fff" stroke-width="1.6"/></svg></span></div>
  </nav>
</header>

<div class="abs photo about-photo" role="img" aria-label="Smiling family with children standing in front of their house"></div>
<h2 class="abs section-title" style="left:401px;top:189px;width:311px">About Us</h2>
<p class="abs copy" style="left:401px;top:225px;width:308px">Lorem ipsum dolor sit amet, consectetur adipiscingsil elit. Vestibulum vestibulum tincidunt orci, nec volutpatli dolor sollicitudin sed. Fusce temph or sodales massa ac cursus. Donec congue eleifejf rpnd est eu placerat. Suspendisse gravida turpis at metus. placerat mattis. Phasellus tincidunt nisl at felis commodo lacinia nec vel quam. Proin auctor enim ipsum. Duis faucibus, ipsum ut ornare viverra, orci dolor mattis massa, ut scelerisque augue mauris vel diam.</p>

<h2 class="abs section-title" style="left:110px;top:432px;width:238px">Executive Team</h2>
<div class="abs member" style="top:485px"><div class="abs photo member-photo" role="img" aria-label="Portrait of executive Marcus Dell" style="background:linear-gradient(135deg,#8fb6dd,#2a62a8)"></div><p class="abs member-bio"><b>Marcus Dell</b>Vestibulum vestibulum tincidunt orci, nec volutpatli dolor sollicitudin sed. Fusce temph or sodales massa ac cursus. Donec congu.</p></div>
<div class="abs member" style="top:595px"><div class="abs photo member-photo" role="img" aria-label="Portrait of executive Clara Benning" style="background:linear-gradient(135deg,#f3ece4,#c9a27a)"></div><p class="abs member-bio"><b>Clara Benning</b>Vestibulum vestibulum tincidunt orci, nec volutpatli dolor sollicitudin sed. Fusce temph or sodales massa ac cursus. Donec congu.</p></div>
<div class="abs member" style="top:700px"><div class="abs photo member-photo" role="img" aria-label="Portrait of executive Nora Fairlie" style="background:linear-gradient(135deg,#f4f1ee,#d2b49c)"></div><p class="abs member-bio"><b>Nora Fairlie</b>Vestibulum vestibulum tincidunt orci, nec volutpatli dolor sollicitudin sed. Fusce temph or sodales massa ac cursus. Donec congu.</p></div>
<div class="abs member" style="top:805px"><div class="abs photo member-photo" role="img" aria-label="Portrait of executive Tessa Rowan" style="background:linear-gradient(135deg,#d7e3d0,#8a5b3e)"></div><p class="abs member-bio"><b>Tessa Rowan</b>Vestibulum vestibulum tincidunt orci, nec volutpatli dolor sollicitudin sed. Fusce temph or sodales massa ac cursus. Donec congu.</p></div>

<h2 class="abs section-title" style="left:401px;top:432px;width:315px">How We Work</h2>
<p class="abs copy" style="left:401px;top:470px;width:308px">Lorem ipsum dolor sit amet, consectetur adipiscingsil elit. Vestibulum vestibulum tincidunt orci, nec volutpatli dolor sollicitudin sed. Fusce temph or sodales massa ac cursus. Donec congue eleifejf rpnd est eu placerat. Suspendisse gravida turpis at metus. placerat mattis. Phasellus tincidunt nisl at felis commodo lacinia nec vel quam. Proin auctor enim ipsum. Duis faucibus, ipsum ut ornare viverra, orci dolor mattis massa, ut scelerisque augue mauris vel diam.</p>

<h2 class="abs section-title" style="left:401px;top:692px;width:315px">Why Choose Us</h2>
<p class="abs copy" style="left:401px;top:729px;width:308px">Lorem ipsum dolor sit amet, consectetur adipiscingsil elit. Vestibulum vestibulum tincidunt orci, nec volutpatli dolor sollicitudin sed. Fusce temph or sodales massa ac cursus. Donec congue eleifejf rpnd est eu placerat. Suspendisse gravida turpis at metus. placerat mattis. Phasellus tincidunt nisl at felis commodo lacinia nec vel quam. Proin auctor enim ipsum. Duis faucibus, ipsum ut ornare viverra, orci dolor mattis massa, ut scelerisque augue mauris vel diam.</p>

<footer class="abs site-footer"></footer>
<div class="abs foot-col" style="left:119px;top:1027px"><h3>About Us</h3><ul><li>Company Info</li><li>Our Services</li><li>Clients</li><li>Partners</li></ul></div>
<div class="abs foot-col" style="left:218px;top:1027px"><h3>Advice</h3><ul><li>Sign up</li><li>Forums</li><li>Promotion</li><li>Career</li></ul></div>
<div class="abs foot-col" style="left:303px;top:1027px"><h3>Join In</h3><ul><li>FAQs</li><li>Solutions</li><li>Sitemap</li><li>Contacts</li></ul></div>
<div class="abs news-title">Join our Newsletter</div>
<div class="abs email">Email Address:</div>
<div class="abs subscribe">Subscribe</div>
<span class="abs social" style="left:642px"></span>
<span class="abs social" style="left:665px"></span>
<span class="abs social" style="left:688px"></span>
<div class="abs foot-rule"></div>
<div class="abs legal">Disclaimer &amp; Terms &amp; Conditions &nbsp;|&nbsp; Privacy Policy &nbsp;| Advertise With Us &nbsp;|&nbsp; Contact Us</div>
<div class="abs copyright">Hearthside Lending Relief &nbsp;© 2012. &nbsp;All Rights Reserved</div>
</body>
</html>
```